Letterhead and matching envelope design for a dental office

We need a new stationary design, letterhead and envelope #10, for a dental office in Denver area. We are called Bright Harbor Dental. We want a simple and minimalistic design but not a boring design. I wish to have one good point that makes it look professional. I have attached our logo. Feel free to use either one. I want the design for letterhead and envelope look like a "matching pair" but not look the same. The envelope doesn't have to be white and it will have an address window on bottom left.

Target Market(s)

everyone who visits dentist (adults)

Industry/Entity Type

Dental

Font styles to use
Other font styles liked:
• close to font on logo or something that matches well

Requirements
Must have
• professional
• simple, minimalistic
• unique point that stands out
Nice to have
• matching but not same design for letterhead and envelope
Should not have
• not look like all the other boring designs
• no flowery, distracting feats

```html
<!DOCTYPE html>
<html lang="en">
<head>
<meta charset="utf-8">
<title>Bright Harbor Dental — Stationery</title>
<link rel="stylesheet" href="https://fonts.googleapis.com/css2?family=Lato:wght@400;700&family=Caveat:wght@500&display=swap">
<style>
  :root{
    --green:#38b34a;
    --green-light:#a9dbb0;
    --green-pale:#eef6ee;
    --ink:#2b2b2b;
    --ink-soft:#555;
    --paper:#ffffff;
    --backdrop:#e6e7e8;
    --signature:#2a2f8f;
  }
  *{box-sizing:border-box;margin:0;padding:0}
  html,body{width:1200px;height:799px;overflow:hidden}
  body{background:var(--backdrop);font-family:"Lato",Arial,sans-serif;color:var(--ink);position:relative}

  .sheet{position:absolute;background:var(--paper);overflow:hidden;box-shadow:0 2px 6px rgba(0,0,0,.12)}

  /* brand name (logo stand-in) */
  .brand{display:flex;align-items:center;gap:7px;font-weight:700;text-transform:uppercase;letter-spacing:.14em;color:var(--green);font-size:12px;white-space:nowrap}
  .brand-dot{width:9px;height:9px;border-radius:50%;background:currentColor;flex:none}
  .brand--white{color:var(--paper)}

  .deco-circle{position:absolute;border-radius:50%;background:var(--green-pale)}

  /* footer band shared by letterhead + envelope front */
  .footer-band{position:absolute;left:0;right:0;bottom:0;height:20px}
  .footer-band .rule-light{position:absolute;left:0;right:0;top:0;height:4px;background:var(--green-light)}
  .footer-band .rule{position:absolute;left:0;right:0;bottom:0;height:12px;background:var(--green)}
  .footer-band .web{position:absolute;right:14px;bottom:1px;font-size:9px;color:var(--paper);letter-spacing:.03em}

  .return-address{position:absolute;font-size:9px;line-height:1.35;color:var(--ink)}
  .return-address .name{color:var(--green)}

  /* letterhead */
  .letterhead{left:70px;top:102px;width:420px;height:594px}
  .letterhead .brand{position:absolute;right:34px;top:42px}
  .letterhead .deco-circle{width:260px;height:260px;left:60px;top:330px}
  .letter{position:absolute;left:40px;top:90px;width:250px;font-size:8px;line-height:1.5;color:var(--ink-soft)}
  .letter .salutation{color:var(--ink);font-weight:700;margin-bottom:8px}
  .letter p{margin-bottom:8px;text-align:justify}
  .letter .closing{color:var(--ink);margin-top:10px}
  .letter .signature{font-family:"Caveat",cursive;font-size:22px;color:var(--signature);line-height:1.1;margin:2px 0}
  .letter .signer{color:var(--ink);line-height:1.4}
  .letterhead .return-address{left:40px;bottom:52px}
  .contact{position:absolute;left:190px;bottom:52px;font-size:9px;line-height:1.6;list-style:none}
  .contact li{display:flex;align-items:center;gap:5px}
  .contact svg{width:10px;height:10px;flex:none}

  /* envelope back */
  .envelope-back{left:560px;top:90px;width:580px;height:252px}
  .envelope-back svg.flap{position:absolute;left:0;top:0}
  .envelope-back .brand{position:absolute;left:360px;top:62px;font-size:11px}

  /* envelope front */
  .envelope-front{left:560px;top:420px;width:580px;height:252px}
  .envelope-front .brand{position:absolute;left:40px;top:34px}
  .envelope-front .deco-circle{width:220px;height:220px;left:120px;top:90px}
  .envelope-front .return-address{left:40px;top:70px}
</style>
</head>
<body>

<section class="sheet letterhead" aria-label="Letterhead">
  <div class="deco-circle" aria-hidden="true"></div>
  <div class="brand"><span class="brand-dot"></span>Bright Harbor Dental</div>

  <article class="letter">
    <div class="salutation">Dear Mr. Carter,</div>
    <p>Lorem ipsum is simply dummy text of the printing and typesetting trade. It has been the standard sample text for many years, used when a printer scrambled type to build a specimen book that still survives today.</p>
    <p>The standard chunk of sample text used since the early days is reproduced below for those interested, along with its exact original form and a later translation.</p>
    <p>Lorem ipsum is simply dummy text of the printing trade. It has survived many centuries and the leap into electronic typesetting, remaining almost unchanged.</p>
    <div class="closing">Sincerely Yours,</div>
    <div class="signature">your name</div>
    <div class="signer">Name Last Name<br>Company Name</div>
  </article>

  <address class="return-address">
    <span class="name">Bright Harbor Dental</span><br>
    2785 Lakeview Blvd.<br>
    Suite 210 Arvada, CO 80004
  </address>

  <ul class="contact">
    <li><svg viewBox="0 0 10 10" aria-hidden="true"><circle cx="5" cy="5" r="5" fill="var(--green)"/><path d="M3.4 2.6l1 1-.5.7a3.5 3.5 0 0 0 1.8 1.8l.7-.5 1 1-.6.8C5 7.3 2.7 5 2.6 3.2z" fill="#fff"/></svg>720-555-0142</li>
    <li><svg viewBox="0 0 10 10" aria-hidden="true"><circle cx="5" cy="5" r="5" fill="var(--green)"/><rect x="2.5" y="3.3" width="5" height="3.4" fill="none" stroke="#fff" stroke-width=".7"/><path d="M2.5 3.3L5 5.2l2.5-1.9" fill="none" stroke="#fff" stroke-width=".7"/></svg>info@brightharbordental.com</li>
  </ul>

  <div class="footer-band">
    <div class="rule-light"></div>
    <div class="rule"></div>
    <span class="web">www.brightharbordental.com</span>
  </div>
</section>

<section class="sheet envelope-back" aria-label="Envelope back">
  <svg class="flap" width="580" height="252" viewBox="0 0 580 252" aria-hidden="true">
    <path d="M0 0H580V150Q580 182 548 176L0 62Z" fill="var(--green)"/>
    <rect x="0" y="240" width="580" height="4" fill="var(--green-light)"/>
    <rect x="0" y="244" width="580" height="8" fill="var(--green)"/>
  </svg>
  <div class="brand brand--white"><span class="brand-dot"></span>Bright Harbor Dental</div>
</section>

<section class="sheet envelope-front" aria-label="Envelope front">
  <div class="deco-circle" aria-hidden="true"></div>
  <div class="brand"><span class="brand-dot"></span>Bright Harbor Dental</div>
  <address class="return-address">
    <span class="name">Bright Harbor Dental</span><br>
    2785 Lakeview Blvd.<br>
    Suite 210 Arvada, CO 80004
  </address>
  <div class="footer-band">
    <div class="rule-light"></div>
    <div class="rule"></div>
    <span class="web">www.brightharbordental.com</span>
  </div>
</section>

</body>
</html>
```